Business Card Design for my Real Estate Investing Company

This is for a Real Estate Investing Company that will be serving the Las Vegas Valley. Id like the following slogan included: "Investing in Our Community" I have attached my logo. You will see the color tones I'm interested in..in my logo. I would like the card to be double-sided with a modern, professional look.
Target Market(s)
Homeowners, banks, real estate industry
Industry/Entity Type
Real Estate
Contact Information for Business Card
name: Dale Harwick
position: Managing Member
address: 4821 Corliss Pkwy ste 207-300
Cedar Hollow, NV 89411
phone: (702) 555-0143
fax: (702) 555-0187
email: SummitRidgeEstate@hollowmail.test
web: SummitRidgeEstates.test
*At the bottom of the card I would like....
We buy houses for cash....no repairs, no commissions, no fees!
Logo Text
SUMMIT RIDGE ESTATES "Investing in Our Community"
Font styles to use
Other font styles liked:
- Lora
Requirements
Must have
- On the back of the card, i'd like to have my logo large and the following statements:
- Are you considering selling your home? Want a simple, hassle-free transaction? We can help! We buy houses for cash and can close quickly! No need to do any repairs, no realtor commissions, no closing costs.....and no headaches. Let us help you with your real estate needs...!
Nice to have
- multiple colors 2 two tone on front and back

```html
<!DOCTYPE html>
<html lang="en">
<head>
<meta charset="utf-8">
<title>Summit Ridge Estates – Business Card</title>
<link rel="stylesheet" href="https://fonts.googleapis.com/css2?family=Lora:wght@400;500&display=swap">
<style>
  :root {
    --brand-blue: #0a5ca9;
    --brand-grey: #97999c;
    --ink: #1d1d1f;
    --paper: #ffffff;
    --backdrop: #2b2b2d;
  }
  * { margin: 0; padding: 0; box-sizing: border-box; }
  html, body {
    width: 1189px; height: 1200px; overflow: hidden;
    background: var(--backdrop);
    font-family: "Lora", Georgia, serif;
  }
  .sheet { position: relative; width: 1189px; height: 1200px; }
  .card {
    position: absolute; left: 164px; width: 860px; height: 491px;
    overflow: hidden;
    box-shadow: 0 6px 18px rgba(0,0,0,.45);
  }
  .card--front { top: 79px; background: var(--brand-blue); color: var(--paper); }
  .card--back { top: 630px; background: var(--paper); color: var(--ink); }

  .wordmark { font-weight: 400; white-space: nowrap; line-height: 1; }
  .tagline { font-size: 17px; font-weight: 400; white-space: nowrap; }

  .card--front .brand {
    position: absolute; left: 0; right: 0; top: 180px; text-align: center;
  }
  .card--front .wordmark { font-size: 38px; }
  .card--front .tagline { margin-top: 18px; }
  .card--front .promise {
    position: absolute; left: 0; right: 0; top: 384px; text-align: center;
    font-size: 21px;
  }

  .side-band { position: absolute; top: 0; right: 0; bottom: 0; width: 150px; background: var(--brand-blue); }
  .side-rule { position: absolute; top: 0; bottom: 0; right: 162px; width: 10px; background: var(--brand-grey); }

  .card--back .brand { position: absolute; left: 39px; top: 100px; }
  .card--back .wordmark { font-size: 34px; color: var(--brand-blue); }
  .card--back .tagline { margin-top: 14px; color: var(--ink); }

  .contact { position: absolute; left: 39px; top: 212px; font-size: 20px; line-height: 1.3; }
  .contact__name { color: var(--brand-blue); font-size: 24px; font-weight: 500; line-height: 1.1; }
  .contact__role { margin-bottom: 22px; }
  .contact__address { margin-bottom: 10px; line-height: 1.35; }
  .contact__list { list-style: none; }
  .contact__list li { display: flex; align-items: center; gap: 10px; height: 27px; }
  .icon { width: 19px; height: 19px; flex: none; }
</style>
</head>
<body>
<main class="sheet">

  <section class="card card--front" aria-label="Card front">
    <div class="brand">
      <div class="wordmark">SUMMIT RIDGE ESTATES</div>
      <div class="tagline">"Investing in Our Community"</div>
    </div>
    <p class="promise">We buy houses for cash....no repairs, no commissions, no fees</p>
  </section>

  <section class="card card--back" aria-label="Card back">
    <div class="side-rule" aria-hidden="true"></div>
    <div class="side-band" aria-hidden="true"></div>

    <div class="brand">
      <div class="wordmark">SUMMIT RIDGE ESTATES</div>
      <div class="tagline">"Investing in Our Community"</div>
    </div>

    <div class="contact">
      <div class="contact__name">DALE HARWICK</div>
      <div class="contact__role">Managing Member</div>
      <div class="contact__address">4821 Corliss Pkwy ste 207-300<br>Cedar Hollow, NV 89411</div>
      <ul class="contact__list">
        <li>
          <svg class="icon" viewBox="0 0 20 20" aria-label="Phone"><rect width="20" height="20" fill="var(--brand-blue)"/><path d="M4 8 Q10 3 16 8 L14 10 L12 8.5 L8 8.5 L6 10 Z M6 11 H14 V15 H6 Z" fill="#fff"/></svg>
          <span>(702) 555-0143</span>
        </li>
        <li>
          <svg class="icon" viewBox="0 0 20 20" aria-label="Fax"><rect width="20" height="20" fill="var(--brand-blue)"/><path d="M6 4 H14 V8 H6 Z M4 9 H16 V14 H4 Z M6 12 H14 V16 H6 Z" fill="#fff"/></svg>
          <span>(702) 555-0187</span>
        </li>
        <li>
          <svg class="icon" viewBox="0 0 20 20" aria-label="Email"><rect width="20" height="20" fill="var(--brand-blue)"/><rect x="4" y="6" width="12" height="8" fill="none" stroke="#fff" stroke-width="1.4"/><path d="M4 6 L10 11 L16 6" fill="none" stroke="#fff" stroke-width="1.4"/></svg>
          <span>SummitRidgeEstate@hollowmail.test</span>
        </li>
        <li>
          <svg class="icon" viewBox="0 0 20 20" aria-label="Website"><rect width="20" height="20" fill="var(--brand-blue)"/><g fill="none" stroke="#fff" stroke-width="1.2"><circle cx="10" cy="10" r="6"/><ellipse cx="10" cy="10" rx="2.6" ry="6"/><path d="M4 10 H16 M5 7 H15 M5 13 H15"/></g></svg>
          <span>SummitRidgeEstates.test</span>
        </li>
      </ul>
    </div>
  </section>

</main>
</body>
</html>
```